Meridale Partners Website

Meridale Partners (MP) provide Analytics & Enterprise Performance Management (EPM) advisory & consultancy services. We are passionate about data and making a difference for our clients by working in partnership with them, helping them on their journey to becoming an Meridale Partner. We deliver insights which give our clients a competitive edge and a much deeper understanding of their organisation.

We need a website which shows who we are, what we do and how we do it.

www.meridale-partners.example is our very basic website at the moment. We want to completely revamp it with a corporate look

```html
<!DOCTYPE html>
<html lang="en">
<head>
<meta charset="utf-8">
<title>Meridale Partners</title>
<link rel="stylesheet" href="https://fonts.googleapis.com/css2?family=Poppins:wght@300;400;500;600;700&display=swap">
<style>
:root{
  --navy:#2b566e;
  --ink:#172a38;
  --orange:#d9692f;
  --text:#5a5f66;
  --pale:#f3f8fb;
  --white:#ffffff;
}
*{box-sizing:border-box;margin:0;padding:0}
html,body{width:1200px;height:3089px;overflow:hidden;background:var(--white)}
body{font-family:'Poppins',sans-serif;color:var(--ink);position:relative}
.abs{position:absolute}
.center{left:0;width:1200px;text-align:center}
.eyebrow{font-size:12px;color:var(--orange);text-transform:uppercase;letter-spacing:.2px}
.section-title{font-size:27px;font-weight:600;color:var(--ink);text-transform:uppercase;line-height:1.4}
.btn{display:flex;align-items:center;justify-content:center;border-radius:20px;font-size:13px;text-transform:uppercase;color:var(--white);background:var(--orange)}
.brand{display:flex;align-items:center;gap:12px}
.brand-mark{width:44px;height:44px;border-radius:50%;background:var(--navy)}
.brand-name{font-size:19px;font-weight:600;color:var(--navy);line-height:1.1;text-transform:uppercase}

/* header */
.nav{top:28px;left:549px;display:flex;gap:36px;font-size:12.5px;color:var(--navy)}
.nav-phone{top:19px;left:1006px;width:134px;height:38px;font-weight:600;text-transform:none;gap:6px}

/* hero */
.hero-title{font-size:55px;font-weight:600;color:var(--ink);line-height:1;white-space:nowrap}
.hero-sub{top:371px;left:65px;font-size:14px;color:var(--navy)}
.hero-deco{top:82px;left:676px;width:524px;height:525px;border-radius:50% 0 0 50%;background:linear-gradient(135deg,#e6eff4,#d3e2ea)}

/* about */
.about{top:690px;left:0;width:1200px;height:353px;background:var(--pale)}
.about p{font-size:14px;color:var(--text);line-height:1.65}

/* services */
.service{width:264px;height:264px;border-radius:50%;background:var(--white);box-shadow:0 6px 22px rgba(23,42,56,.1);display:flex;flex-direction:column;align-items:center;justify-content:center;text-align:center;padding:0 42px}
.service.featured{border:22px solid var(--ink);box-shadow:none;padding:0 12px}
.service-icon{width:58px;height:58px;border-radius:14px;background:linear-gradient(135deg,#f3d3bf,#c8d7e0);margin-bottom:12px;flex:none}
.service.featured .service-icon{width:50px;height:50px;margin-bottom:8px}
.service h3{font-size:17px;font-weight:500;color:var(--ink);margin-bottom:6px;white-space:nowrap}
.service p{font-size:14px;color:var(--text);line-height:1.6}
.service.featured p{padding:0 22px}
.read-more{font-size:12px;color:var(--orange);margin-top:8px;display:flex;align-items:center;gap:4px}

/* testimonials */
.testimonials{top:1549px;left:0;width:1200px;height:388px;background:var(--ink)}
.testimonials .section-title{color:var(--white)}
.quote p{font-size:14px;color:var(--white);line-height:1.62}
.arrow{width:36px;height:36px;border-radius:50%;display:flex;align-items:center;justify-content:center}

/* process */
.step-label{font-size:17px;font-weight:500;color:var(--ink);width:192px;text-align:center;top:2307px}

/* contact band */
.cta{top:2461px;left:0;width:1200px;height:300px;background:var(--orange)}
.cta-photo{top:2416px;left:0;width:374px;height:374px;border-radius:50%;background:linear-gradient(135deg,#c8d6e2,#2b566e)}
.cta h2{font-size:28px;font-weight:600;color:var(--white)}
.cta p{font-size:14px;color:var(--white);line-height:1.6}

/* footer */
.footer-head{font-size:14px;font-weight:500;color:var(--ink);padding-bottom:6px;border-bottom:1px solid var(--orange);display:inline-block}
.footer-link{font-size:12px;color:var(--ink);text-transform:uppercase}
.footer-text{font-size:12px;color:var(--text);line-height:1.7;white-space:nowrap}
.social{width:34px;height:34px;border-radius:50%;display:flex;align-items:center;justify-content:center;font-size:7.5px;font-weight:500}
.contact-line{display:flex;align-items:flex-start;gap:10px;font-size:12.5px;color:var(--text);line-height:1.5}
.copyright{top:3065px;font-size:12px;color:var(--ink)}
</style>
</head>
<body>

<!-- Header -->
<header>
  <div class="abs brand" style="top:14px;left:60px">
    <span class="brand-mark"></span>
    <span class="brand-name">Meridale<br>Partners</span>
  </div>
  <nav class="abs nav">
    <span>WHO WE ARE</span><span>WHAT WE DO</span><span>HOW WE DO IT</span><span>CONTACT US</span>
  </nav>
  <a class="abs btn nav-phone">
    <svg width="18" height="18" viewBox="0 0 24 24" fill="none" stroke="#fff" stroke-width="1.8"><path d="M5 3h4l2 5-2.5 1.5a11 11 0 0 0 6 6L16 13l5 2v4a2 2 0 0 1-2 2A16 16 0 0 1 3 5a2 2 0 0 1 2-2z"/></svg>
    01 555 0142
  </a>
</header>

<!-- Hero -->
<section>
  <div class="abs hero-deco" role="img" aria-label="Large decorative brand shape"></div>
  <h1 class="abs hero-title" style="top:224px;left:62px">MERIDALE</h1>
  <div class="abs hero-title" style="top:294px;left:185px">PARTNERS</div>
  <p class="abs hero-sub">DATA ANALYTICS &amp; EPM Consulting Services</p>
  <a class="abs btn" style="top:444px;left:60px;width:118px;height:37px">Contact us</a>
</section>

<!-- About -->
<section class="abs about">
  <div class="abs eyebrow center" style="top:53px">Who we are</div>
  <h2 class="abs section-title center" style="top:72px">Welcome to Meridale<br>Partners</h2>
  <p class="abs" style="top:154px;left:340px;width:520px;text-align:center">MP are a Data Analytics &amp; EPM company, specialising in the implementation and support of Business Intelligence, EPM and Data Analytics business solutions, both in the Cloud and on-premise.</p>
  <a class="abs btn" style="top:263px;left:547px;width:106px;height:37px">Read more</a>
</section>

<!-- Services -->
<section>
  <div class="abs eyebrow center" style="top:1124px">Our services</div>
  <h2 class="abs section-title center" style="top:1143px">What we do</h2>
  <div class="abs service" style="top:1201px;left:136px">
    <div class="service-icon" role="img" aria-label="Advisory icon"></div>
    <h3>Advise &amp; Architech</h3>
    <p>Helping our customers understand the art of the possible...</p>
    <span class="read-more">READ MORE <svg width="22" height="10" viewBox="0 0 22 10" fill="none" stroke="#d9692f" stroke-width="1.5"><path d="M0 5h20M16 1l4 4-4 4"/></svg></span>
  </div>
  <div class="abs service featured" style="top:1201px;left:468px">
    <div class="service-icon" role="img" aria-label="Design icon"></div>
    <h3>Design &amp; Implement</h3>
    <p>Working with the project management team, through each stage...</p>
    <span class="read-more">READ MORE <svg width="22" height="10" viewBox="0 0 22 10" fill="none" stroke="#d9692f" stroke-width="1.5"><path d="M0 5h20M16 1l4 4-4 4"/></svg></span>
  </div>
  <div class="abs service" style="top:1201px;left:800px">
    <div class="service-icon" role="img" aria-label="Managed services icon"></div>
    <h3>Optimse&amp;Manage</h3>
    <p>Our Managed Services delivers proactive, on-demand support...</p>
    <span class="read-more">READ MORE <svg width="22" height="10" viewBox="0 0 22 10" fill="none" stroke="#d9692f" stroke-width="1.5"><path d="M0 5h20M16 1l4 4-4 4"/></svg></span>
  </div>
</section>

<!-- Testimonials -->
<section class="abs testimonials">
  <div class="abs eyebrow center" style="top:52px">Our testimonials</div>
  <h2 class="abs section-title center" style="top:71px">What our client says...</h2>
  <div class="abs" role="img" aria-label="Client portrait" style="top:129px;left:568px;width:76px;height:76px;border-radius:50%;border:3px solid #fff;background:linear-gradient(135deg,#cfd8de,#7b8a94)"></div>
  <div class="abs" style="top:127px;left:553px;width:32px;height:32px;border-radius:50%;background:var(--orange);display:flex;align-items:center;justify-content:center">
    <svg width="16" height="14" viewBox="0 0 16 14" fill="#fff"><path d="M0 8a6 6 0 0 1 6-6v2a4 4 0 0 0-3 3h3v6H0zM9 8a6 6 0 0 1 6-6v2a4 4 0 0 0-3 3h3v6H9z"/></svg>
  </div>
  <div class="abs eyebrow center" style="top:218px">Client name</div>
  <div class="abs quote" style="top:243px;left:328px;width:544px;text-align:center">
    <p>Lorem Ipsum is simply dummy text of the printing and typesetting industry. Lorem Ipsum has been the industry's standard dummy text ever since the 1500s, when an unknown printer took a galley of type and scrambled it to make a type specimen book.</p>
  </div>
  <span class="abs arrow" style="top:215px;left:168px;background:var(--navy)"><svg width="10" height="16" viewBox="0 0 10 16" fill="none" stroke="#fff" stroke-width="1.6"><path d="M8 2L2 8l6 6"/></svg></span>
  <span class="abs arrow" style="top:215px;left:996px;background:var(--orange)"><svg width="10" height="16" viewBox="0 0 10 16" fill="none" stroke="#fff" stroke-width="1.6"><path d="M2 2l6 6-6 6"/></svg></span>
</section>

<!-- Process -->
<section>
  <div class="abs eyebrow center" style="top:2018px">Process</div>
  <h2 class="abs section-title center" style="top:2037px">How we do it</h2>
  <svg class="abs" style="top:2085px;left:0" width="1200" height="220" viewBox="0 0 1200 220" fill="none">
    <path d="M118 110 A96 96 0 0 0 310 110" stroke="#172a38" stroke-width="3"/>
    <path d="M310 110 A96 96 0 0 1 502 110" stroke="#d9692f" stroke-width="3"/>
    <path d="M502 110 A96 96 0 0 0 694 110" stroke="#172a38" stroke-width="3"/>
    <path d="M694 110 A96 96 0 0 1 886 110" stroke="#d9692f" stroke-width="3"/>
    <path d="M886 110 A96 96 0 0 0 1080 110" stroke="#172a38" stroke-width="3"/>
    <circle cx="214" cy="110" r="72" stroke="#d9692f" stroke-width="3" fill="#fff"/>
    <circle cx="408" cy="110" r="72" stroke="#172a38" stroke-width="3" fill="#fff"/>
    <circle cx="600" cy="110" r="72" stroke="#d9692f" stroke-width="3" fill="#fff"/>
    <circle cx="792" cy="110" r="72" stroke="#172a38" stroke-width="3" fill="#fff"/>
    <circle cx="985" cy="110" r="72" stroke="#d9692f" stroke-width="3" fill="#fff"/>
    <g stroke-width="3" fill="#fff">
      <circle cx="118" cy="110" r="6" stroke="#172a38"/>
      <circle cx="310" cy="110" r="6" stroke="#172a38"/>
      <circle cx="502" cy="110" r="6" stroke="#d9692f"/>
      <circle cx="694" cy="110" r="6" stroke="#172a38"/>
      <circle cx="886" cy="110" r="6" stroke="#d9692f"/>
      <circle cx="1080" cy="110" r="6" stroke="#172a38"/>
    </g>
    <g role="img" aria-label="Step icons">
      <circle cx="214" cy="110" r="28" fill="#f6e1d4"/>
      <circle cx="408" cy="110" r="28" fill="#e2e8ec"/>
      <rect x="574" y="82" width="52" height="56" rx="6" fill="#f6e1d4"/>
      <circle cx="792" cy="110" r="28" fill="#e2e8ec"/>
      <g fill="#172a38"><rect x="953" y="118" width="10" height="22"/><rect x="969" y="108" width="10" height="32"/><rect x="985" y="98" width="10" height="42"/><rect x="1001" y="88" width="10" height="52"/></g>
      <path d="M950 104 L1010 74" stroke="#d9692f" stroke-width="4"/>
    </g>
  </svg>
  <div class="abs step-label" style="left:120px">Idea</div>
  <div class="abs step-label" style="left:312px">Strategy</div>
  <div class="abs step-label" style="left:504px">Plan</div>
  <div class="abs step-label" style="left:696px">Team Work</div>
  <div class="abs step-label" style="left:889px">Growth</div>
</section>

<!-- Call to action -->
<section>
  <div class="abs cta"></div>
  <div class="abs cta-photo" role="img" aria-label="Photo of a support consultant wearing a headset at a desk"></div>
  <div class="abs cta" style="background:none">
    <h2 class="abs" style="top:66px;left:467px">Contact Us to Discuss Your Business Needs</h2>
    <p class="abs" style="top:108px;left:467px;width:600px">Lorem Ipsum is simply dummy text of the printing and typesetting industry. Lorem Ipsum has been the industry's</p>
    <a class="abs btn" style="top:189px;left:461px;width:132px;height:37px;background:var(--ink);text-transform:none;font-weight:600;gap:6px">
      <svg width="18" height="18" viewBox="0 0 24 24" fill="none" stroke="#fff" stroke-width="1.8"><path d="M5 3h4l2 5-2.5 1.5a11 11 0 0 0 6 6L16 13l5 2v4a2 2 0 0 1-2 2A16 16 0 0 1 3 5a2 2 0 0 1 2-2z"/></svg>
      01 555 0142
    </a>
    <a class="abs btn" style="top:189px;left:614px;width:108px;height:37px;background:var(--white);color:var(--ink);text-transform:none">Contact Us</a>
  </div>
</section>

<!-- Footer -->
<footer>
  <div class="abs brand" style="top:2846px;left:60px">
    <span class="brand-mark"></span>
    <span class="brand-name">Meridale<br>Partners</span>
  </div>
  <p class="abs footer-text" style="top:2909px;left:61px">MP are a Data Analytics &amp; EPM company,<br>specialising in the implementation.</p>
  <div class="abs social" style="top:2964px;left:60px;border:1.5px solid var(--ink);color:var(--ink)">Chirp</div>
  <div class="abs social" style="top:2964px;left:107px;background:var(--orange);color:#fff">Linkr</div>

  <div class="abs" style="top:2853px;left:338px"><span class="footer-head">Quick Links</span></div>
  <div class="abs footer-link" style="top:2902px;left:338px">Who we are</div>
  <div class="abs footer-link" style="top:2933px;left:338px">What we do</div>
  <div class="abs footer-link" style="top:2964px;left:338px">How we do it</div>
  <div class="abs footer-link" style="top:2996px;left:338px">Contact us</div>

  <div class="abs" style="top:2853px;left:616px"><span class="footer-head">Contact Us</span></div>
  <div class="abs contact-line" style="top:2900px;left:614px;width:250px">
    <svg width="20" height="22" viewBox="0 0 20 22" fill="none" stroke="#2b566e" stroke-width="1.4"><path d="M10 21s7-7 7-12a7 7 0 0 0-14 0c0 5 7 12 7 12z"/><circle cx="10" cy="9" r="2.5"/></svg>
    <span>12 Harbour Lane, Northgate,<br>Dublin 4, D04 XK21</span>
  </div>
  <div class="abs contact-line" style="top:2950px;left:614px;font-weight:600;color:var(--navy)">
    <svg width="18" height="18" viewBox="0 0 24 24" fill="none" stroke="#2b566e" stroke-width="1.6"><path d="M5 3h4l2 5-2.5 1.5a11 11 0 0 0 6 6L16 13l5 2v4a2 2 0 0 1-2 2A16 16 0 0 1 3 5a2 2 0 0 1 2-2z"/></svg>
    01 555 0142
  </div>
  <div class="abs contact-line" style="top:2986px;left:614px">
    <svg width="20" height="16" viewBox="0 0 20 16" fill="none" stroke="#2b566e" stroke-width="1.4"><rect x="1" y="1" width="18" height="14"/><path d="M1 1l9 8 9-8"/></svg>
    info@meridale-partners.example
  </div>

  <div class="abs" style="top:2853px;left:891px"><span class="footer-head">Our Partner</span></div>
  <div class="abs" style="top:2898px;left:891px;display:flex;align-items:center;gap:10px;font-size:12px">
    <span style="font-weight:600;color:var(--orange)">Veltora</span>
    <span style="width:2px;height:30px;background:var(--orange)"></span>
    <span style="color:var(--ink)">Partner</span>
  </div>

  <div class="abs" style="top:3054px;left:0;width:1200px;height:1px;background:#c9cfd4"></div>
  <div class="abs copyright center">2022© <b style="font-weight:600">MERIDALE PARTNERS</b>. All right reserved.</div>
</footer>

</body>
</html>
```